BVM Marketing Postcard

Design a 2 Sided marketing postcard for our Real estate management caompany. Looking for a professional yet fresh look that will be printed on a 6"x9" glossy flier

Contact information is www.brixleymanagement.example brixleymanagement@postwellmail.example and 555-014-7283

WE are targeting small condo and town home properties to take on their administrative responsibilities of management

```html
<!DOCTYPE html>
<html lang="en">
<head>
<meta charset="utf-8">
<title>BVM Marketing Postcard</title>
<link rel="stylesheet" href="https://fonts.googleapis.com/css2?family=Montserrat:wght@700;800&family=Questrial&family=Open+Sans:ital,wght@1,600&display=swap">
<style>
  :root {
    --page: #e9edf1;
    --card-edge: #ffffff;
    --blue: #1b7fc4;
    --blue-dark: #0f5f9c;
    --blue-light: #3fa0dc;
    --navy-strip: #1d2e3f;
    --orange: #f08a24;
    --orange-dark: #d9701a;
    --ink: #2c3a47;
    --rule: rgba(255,255,255,0.85);
    --panel-bg: #eef4f9;
    --white: #ffffff;
  }
  * { box-sizing: border-box; margin: 0; padding: 0; }
  html, body { width: 800px; height: 1200px; overflow: hidden; }
  body { background: var(--page); font-family: "Questrial", "Century Gothic", sans-serif; color: var(--ink); position: relative; }

  .postcard {
    position: absolute; left: 25px; width: 750px; height: 500px;
    background: var(--card-edge); padding: 7px;
    box-shadow: 0 4px 14px rgba(0,0,0,0.18);
  }
  .postcard--front { top: 60px; }
  .postcard--back { top: 640px; }
  .postcard__inner { position: relative; width: 100%; height: 100%; overflow: hidden; }

  .title-band {
    height: 62px; background: linear-gradient(180deg, var(--blue-light), var(--blue) 60%, var(--blue-dark));
    display: flex; align-items: center; justify-content: center;
    color: var(--white); font-family: "Montserrat", sans-serif; font-weight: 800;
    font-size: 23px; letter-spacing: 0.3px;
  }
  .title-band .abbr { font-weight: 700; }

  /* Front */
  .front-body {
    position: absolute; top: 62px; left: 0; right: 0; bottom: 0;
    background: linear-gradient(160deg, #f7fafd 0%, #dfeaf3 45%, #c9dae8 100%);
  }
  .tagline {
    height: 25px; background: var(--navy-strip); color: var(--white);
    font-family: "Open Sans", sans-serif; font-style: italic; font-weight: 600;
    font-size: 14px; display: flex; align-items: center; justify-content: center;
  }
  .columns { position: absolute; top: 25px; left: 28px; right: 28px; display: flex; }
  .column { width: 50%; }
  .column + .column { border-left: 1px solid var(--rule); }
  .section-head {
    height: 31px; background: linear-gradient(180deg, var(--blue-light), var(--blue));
    color: var(--white); font-family: "Montserrat", sans-serif; font-weight: 700;
    font-size: 16px; display: flex; align-items: center; justify-content: center;
    border-bottom: 2px solid var(--white);
  }
  .list { list-style: none; background: rgba(255,255,255,0.55); }
  .list li {
    position: relative; padding: 0 12px 0 30px; font-size: 11.2px; line-height: 1.25;
    border-bottom: 1px solid var(--rule); display: flex; align-items: center;
  }
  .list li::before {
    content: ""; position: absolute; left: 17px; top: 50%; margin-top: -7px;
    width: 5px; height: 5px; border-radius: 50%; background: var(--orange);
  }
  .list--who li { height: 42px; }
  .list--why li { height: 37px; }
  .list--why li:first-child { height: 50px; }
  .list--what li { height: 33px; }
  .list--what li:nth-child(1), .list--what li:nth-child(2), .list--what li:nth-child(3) { height: 42px; }
  .list--what li:nth-child(5) { height: 48px; }
  .list--what li:nth-child(8) { height: 35px; }
  .list em { font-style: italic; }

  .contact-tab {
    position: absolute; left: 50%; transform: translateX(-50%);
    height: 26px; padding: 0 40px; color: var(--white); font-size: 12.5px;
    display: flex; align-items: center; gap: 6px; white-space: nowrap;
  }
  .contact-tab--front { bottom: 7px; }
  .contact-tab--front svg.tab-shape { position: absolute; inset: 0; width: 100%; height: 100%; z-index: 0; }
  .contact-tab > *:not(.tab-shape) { position: relative; z-index: 1; }
  .icon { width: 12px; height: 12px; flex: none; }

  /* Back */
  .back-panel {
    position: absolute; top: 62px; left: 0; width: 357px; bottom: 0;
    background: linear-gradient(180deg, var(--blue) 0%, var(--blue-dark) 100%);
  }
  .back-list { list-style: none; padding: 20px 16px 0 24px; color: var(--white); }
  .back-list li { position: relative; font-size: 12.8px; line-height: 1.3; margin-bottom: 14px; padding-left: 16px; }
  .back-list li::before {
    content: ""; position: absolute; left: 0; top: 6px; width: 5px; height: 5px;
    border-radius: 50%; background: var(--white);
  }
  .back-footer {
    position: absolute; left: 0; width: 357px; bottom: 8px; height: 48px;
    background: linear-gradient(180deg, var(--orange), var(--orange-dark));
    color: var(--white); font-size: 13px; display: flex; align-items: center; gap: 6px; padding-left: 12px;
  }
  .photo {
    position: absolute; top: 62px; left: 357px; right: 0; bottom: 0;
    background: linear-gradient(180deg, #9fc7e8 0%, #d5e6f2 30%, #6e8a6a 48%, #4f8f3a 62%, #7ec24a 100%);
  }
</style>
</head>
<body>

<section class="postcard postcard--front">
  <div class="postcard__inner">
    <header class="title-band">BRIXLEY VALE MANAGEMENT LLC&nbsp;<span class="abbr">(“BVM”)</span></header>
    <div class="front-body">
      <p class="tagline">Improve compliance, reporting, and communication amongst all owners and board members</p>
      <div class="columns">
        <div class="column">
          <h2 class="section-head">WHO WE ARE</h2>
          <ul class="list list--who">
            <li>A professional services organization with a focus on small (3-10 unit) residential buildings</li>
            <li>Over 30 years of combined experience in real estate and property management</li>
            <li>Professional, courteous, timely service that is technologically driven</li>
          </ul>
          <h2 class="section-head">Why use BVM?</h2>
          <ul class="list list--why">
            <li>Owners are rarely suited to manage associations and the burden often falls unfairly on one or two individuals to do all the work</li>
            <li>Low monthly fees tailored to your needs</li>
            <li>The association's board of directors maintains control of all decision making</li>
          </ul>
        </div>
        <div class="column">
          <h2 class="section-head">WHAT WE DO</h2>
          <ul class="list list--what">
            <li>Remove the administrative burden of managing small residential buildings</li>
            <li>Utilize economies of scale to reduce expenses for all owners across a wide variety of service providers</li>
            <li>Collect all assessments and pay all bills</li>
            <li>Provide monthly accounting reconciliation and reporting</li>
            <li><span>Provide access to BVM's client portal with a central repository of all association materials <em>(bylaws, financials, meeting minutes, communications, etc)</em></span></li>
            <li>Issue 1099s to all contractors as required by law</li>
            <li>Prepare year-end financial statements</li>
            <li>Lender and legal HOA documents for mortgage companies and sales</li>
          </ul>
        </div>
      </div>
      <div class="contact-tab contact-tab--front">
        <svg class="tab-shape" viewBox="0 0 100 26" preserveAspectRatio="none" aria-hidden="true"><polygon points="0,0 100,0 96,26 4,26" fill="#f08a24"/></svg>
        <svg class="icon" viewBox="0 0 12 12" aria-hidden="true"><circle cx="6" cy="6" r="5" fill="none" stroke="#fff" stroke-width="1.2"/><circle cx="6" cy="6" r="2" fill="#fff"/></svg>
        <span>www.brixleymanagement.example&nbsp;|</span>
        <svg class="icon" viewBox="0 0 12 12" aria-hidden="true"><path d="M3 1 L5 3.5 L4 5 Q5.5 7.5 7 8 L8.5 7 L11 9 L9.5 11 Q4 10.5 1 3 Z" fill="none" stroke="#fff" stroke-width="1"/></svg>
        <span>555-014-7283</span>
      </div>
    </div>
  </div>
</section>

<section class="postcard postcard--back">
  <div class="postcard__inner">
    <header class="title-band">BRIXLEY VALE MANAGEMENT LLC&nbsp;<span class="abbr">(“BVM”)</span></header>
    <div class="back-panel">
      <ul class="back-list">
        <li>Cost effective property management solution for 3-10 unit buildings</li>
        <li>Prices starting as low as $100/month</li>
        <li>Utilize our economies of scale to reduce costs across existing services (trash, insurance, maintenance, etc)</li>
        <li>Eliminate the unfair burden placed on a few owners to do all the work while others free-ride</li>
        <li>Improve communication amongst all owners and board members</li>
        <li>The association's board of directors maintain all decision-making power</li>
        <li>Utilize our vetted service providers for prompt job completion and fair pricing</li>
      </ul>
    </div>
    <div class="back-footer">
      <svg class="icon" viewBox="0 0 12 12" aria-hidden="true"><circle cx="6" cy="6" r="5" fill="none" stroke="#fff" stroke-width="1.2"/><circle cx="6" cy="6" r="2" fill="#fff"/></svg>
      <span>www.brixleymanagement.example&nbsp;|</span>
      <svg class="icon" viewBox="0 0 12 12" aria-hidden="true"><path d="M3 1 L5 3.5 L4 5 Q5.5 7.5 7 8 L8.5 7 L11 9 L9.5 11 Q4 10.5 1 3 Z" fill="none" stroke="#fff" stroke-width="1"/></svg>
      <span>555-014-7283</span>
    </div>
    <div class="photo" role="img" aria-label="Photo of a residential building behind leafy trees and a green lawn under a blue sky with clouds"></div>
  </div>
</section>

</body>
</html>
```